High-end construction company needs a business card design

We need a modern looking business card that draws people in, is memorable and looks so good people will want to sick it on their fridges.
On the first side what is needed are:
Logo
My name - Tomasz Brelwik
Title - Managing Director
Website - www.varkelt.co.uk
Email - tomasz@varkelt.co.uk
Telephone - 020 5194 6281
Mobile - 07845139072
On the back side was is needed is a list of all the services we provide:
-Kitchen Renovations
-Bathroom Renovations
-House Renovations
-Garage Conversions
-Extensions
-Loft Conversions
-Conservatories
-Carpentry
-Tiling
-Electrical
-Plumbing & Heating
-Bricklaying
-Landscaping
-Decorating
-Plastering
We would like the colours to be the same shades as on the logo with grey or black for the words.
Target Market(s)
Anyone who needs building work done
Contact Information for Business Card
This business card is for a construction company which strives to deliver excellent service and quality.
The look and feel of the card should represent this.
Requirements
Must have
- On the first side what is needed are:
Logo
My name - Tomasz Brelwik
Title - Managing Director
Website - www.varkelt.co.uk
Email - tomasz@varkelt.co.uk
Telephone - 020 5194 6281
Mobile - 07845139072
Nice to have
- Cool looking features

```html
<!DOCTYPE html>
<html lang="en">
<head>
<meta charset="utf-8">
<title>Varkelt Construction – Business Card</title>
<link rel="stylesheet" href="https://fonts.googleapis.com/css2?family=Roboto+Condensed:wght@300;700&family=Roboto:wght@400;700&display=swap">
<style>
  :root {
    --bg: #e6e6e6;
    --green-light: #72b843;
    --green: #5aa83c;
    --green-dark: #4a8f3a;
    --card-white: #f4f4f4;
    --ink: #3a3a3a;
  }
  * { margin: 0; padding: 0; box-sizing: border-box; }
  html, body { width: 1200px; height: 960px; overflow: hidden; background: var(--bg); }
  .canvas { position: relative; width: 1200px; height: 960px; }

  .card { position: absolute; left: 338px; width: 528px; height: 342px; overflow: hidden; }

  /* Services side */
  .card--services { top: 127px; background: linear-gradient(100deg, var(--green-light) 0%, var(--green) 45%, var(--green-dark) 100%); }
  .illustration {
    position: absolute; left: 0; top: 40px; width: 240px; height: 250px;
    background: linear-gradient(135deg, rgba(255,255,255,.35), rgba(255,255,255,.12));
    clip-path: polygon(0 70%, 55% 15%, 75% 0, 100% 45%, 100% 100%, 0 100%);
  }
  .web-band {
    position: absolute; left: 0; top: 296px; width: 244px; height: 24px;
    background: var(--green-dark);
    clip-path: polygon(0 0, 92% 0, 100% 100%, 0 100%);
    font: 400 13px/24px "Roboto", sans-serif; color: #fff; padding-left: 46px;
  }
  .services { position: absolute; right: 21px; top: 20px; text-align: right; font-family: "Roboto Condensed", sans-serif; color: #fff; }
  .services li { list-style: none; white-space: nowrap; line-height: 24.7px; height: 24.7px; }
  .svc { font-size: 27px; letter-spacing: -.2px; }
  .svc--bold { font-weight: 700; }
  .svc--light { font-weight: 300; }
  .svc--sm { font-size: 22px; }
  .svc--xs { font-size: 20px; }

  /* Contact side */
  .card--contact { top: 508px; background: var(--card-white); }
  .brand { position: absolute; left: 45px; top: 100px; color: var(--green); font: 700 46px/1 "Roboto Condensed", sans-serif; letter-spacing: 1px; }
  .brand small { display: block; font-size: 13px; letter-spacing: 1.6px; margin-top: 3px; margin-left: 2px; }
  .person { position: absolute; right: 40px; top: 81px; text-align: right; }
  .person__name { font: 700 17px/1.2 "Roboto", sans-serif; color: var(--green-dark); letter-spacing: .3px; }
  .person__title { font: 400 14px/1.3 "Roboto", sans-serif; color: var(--ink); }
  .accent-bar { position: absolute; right: 0; top: 77px; width: 14px; height: 45px; background: var(--green-light); }
  .contacts { position: absolute; left: 45px; top: 223px; font: 400 14px/18.5px "Roboto", sans-serif; color: var(--ink); }
  .contacts li { list-style: none; display: flex; align-items: center; gap: 5px; }
  .contacts svg { width: 13px; height: 13px; fill: var(--green-dark); flex: none; }
  .foot-band { position: absolute; left: 0; bottom: 0; width: 100%; height: 17px; background: var(--green-dark); }
  .foot-band::after { content: ""; position: absolute; right: 0; top: 0; width: 132px; height: 100%; background: var(--green-light); clip-path: polygon(14px 0, 100% 0, 100% 100%, 0 100%); }
</style>
</head>
<body>
<main class="canvas">

  <section class="card card--services" aria-label="Services">
    <div class="illustration" role="img" aria-label="Illustration of an excavator arm over a house and city buildings"></div>
    <div class="web-band">www.varkelt.co.uk</div>
    <ul class="services">
      <li><span class="svc svc--bold" style="opacity:.55">HOUSE RENOVATIONS</span> <span class="svc svc--light" style="opacity:.8">TILING</span></li>
      <li><span class="svc svc--light" style="opacity:.75">PLASTERING</span> <span class="svc svc--bold" style="opacity:.85">ELECTRICAL</span></li>
      <li><span class="svc svc--light svc--sm" style="opacity:.8">KITCHEN RENOVATIONS</span></li>
      <li><span class="svc svc--bold svc--sm" style="opacity:.5">BATHROOM RENOVATIONS</span></li>
      <li><span class="svc svc--light svc--sm" style="opacity:.85">GARAGE CONVERSIONS</span></li>
      <li><span class="svc svc--light svc--xs" style="opacity:.6">EXTENSIONS</span><span class="svc svc--bold" style="opacity:.9">CARPENTRY</span></li>
      <li><span class="svc svc--bold svc--sm" style="opacity:.5">LANDSCAPING</span></li>
      <li><span class="svc svc--bold svc--sm" style="opacity:.8">LOFT CONVERSIONS</span></li>
      <li><span class="svc svc--light svc--xs" style="opacity:.35">CONSERVATORIES</span></li>
      <li><span class="svc svc--bold" style="opacity:.9">BRICKLAYING</span></li>
      <li><span class="svc svc--light svc--xs" style="opacity:.45">PLUMBING &amp; HEATING</span></li>
      <li><span class="svc svc--light svc--xs" style="opacity:.8">DECORATING</span> <span class="svc svc--bold" style="opacity:.85">ELECTRICAL</span></li>
    </ul>
  </section>

  <section class="card card--contact" aria-label="Contact details">
    <div class="brand">VARKELT<small>CONSTRUCTION LTD</small></div>
    <div class="person">
      <p class="person__name">TOMASZ BRELWIK</p>
      <p class="person__title">Managing Director</p>
    </div>
    <div class="accent-bar"></div>
    <ul class="contacts">
      <li><svg viewBox="0 0 24 24"><path d="M6.6 10.8a15 15 0 0 0 6.6 6.6l2.2-2.2a1 1 0 0 1 1-.25 11.4 11.4 0 0 0 3.6.57 1 1 0 0 1 1 1V20a1 1 0 0 1-1 1A17 17 0 0 1 3 4a1 1 0 0 1 1-1h3.5a1 1 0 0 1 1 1c0 1.25.2 2.45.57 3.57a1 1 0 0 1-.25 1z"/></svg>020 5194 6281</li>
      <li><svg viewBox="0 0 24 24"><path d="M7 1h10a2 2 0 0 1 2 2v18a2 2 0 0 1-2 2H7a2 2 0 0 1-2-2V3a2 2 0 0 1 2-2zm0 3v14h10V4zm5 15.2a1 1 0 1 0 0 2 1 1 0 0 0 0-2z"/></svg>07845139072</li>
      <li><svg viewBox="0 0 24 24"><path d="M2 5h20v14H2zm2 2v.5l8 5 8-5V7zm0 3v7h16v-7l-8 5z"/></svg>tomasz@varkelt.co.uk</li>
      <li><svg viewBox="0 0 24 24"><path d="M12 2a10 10 0 1 0 0 20 10 10 0 0 0 0-20zm6.9 6h-3a15 15 0 0 0-1.3-3.9A8 8 0 0 1 18.9 8zM12 4c.8 1.2 1.5 2.5 1.9 4h-3.8c.4-1.5 1.1-2.8 1.9-4zM4.3 14a8 8 0 0 1 0-4h3.4a16 16 0 0 0 0 4zm.8 2h3a15 15 0 0 0 1.3 3.9A8 8 0 0 1 5.1 16zm3-8h-3a8 8 0 0 1 4.3-3.9A15 15 0 0 0 8.1 8zM12 20c-.8-1.2-1.5-2.5-1.9-4h3.8c-.4 1.5-1.1 2.8-1.9 4zm2.3-6H9.7a14 14 0 0 1 0-4h4.6a14 14 0 0 1 0 4zm.3 5.9a15 15 0 0 0 1.3-3.9h3a8 8 0 0 1-4.3 3.9zm1.7-5.9a16 16 0 0 0 0-4h3.4a8 8 0 0 1 0 4z"/></svg>www.varkelt.co.uk</li>
    </ul>
    <div class="foot-band"></div>
  </section>

</main>
</body>
</html>
```